General contractor/GM consaltant business card

I need a card for my contracting company in North Dakota, we build industrial buildings for the oil feild and oil feild related companies offices, shops, airplain hangars, airports ext. We have a familly atmosphere on the job and are very relational and personal.
Industry/Entity Type
Industrial
Contact Information for Business Card
Ridgepost Contractors LLC.
Derek T.Holloway
4837 Tamarind dr. Colorado Springs, CO. 80917
Cell# 406-555-0148
derek@ridgepostcontractors.com

```html
<!DOCTYPE html>
<html lang="en">
<head>
<meta charset="utf-8">
<title>Ridgepost Contractors LLC. – Business Card</title>
<link rel="stylesheet" href="https://fonts.googleapis.com/css2?family=Montserrat:wght@400;500;600;700&display=swap">
<style>
  :root {
    --stage-light: #eeeff0;
    --stage-dark: #b9bbbd;
    --card-white: #ffffff;
    --card-black: #000000;
    --charcoal: #2a2b2e;
    --accent-yellow: #ffcc00;
    --icon-red: #b3121b;
    --text-dark: #1a1a1a;
    --text-light: #ffffff;
    --pattern-tone: #1c1c1c;
  }
  * { margin: 0; padding: 0; box-sizing: border-box; }
  html, body { width: 1200px; height: 1200px; overflow: hidden; }
  body {
    background: radial-gradient(circle at 50% 45%, var(--stage-light) 0%, var(--stage-dark) 100%);
    font-family: "Montserrat", sans-serif;
    position: relative;
  }
  .card {
    position: absolute;
    left: 228px;
    width: 742px;
    overflow: hidden;
  }
  .card-front { top: 172px; height: 420px; background: var(--card-black); }
  .card-back { top: 600px; height: 422px; background: var(--card-black); }

  .front-header {
    position: absolute; left: 0; top: 0;
    width: 742px; height: 214px;
    background: var(--card-white);
  }
  .front-header svg { position: absolute; left: 0; top: 0; }

  .brand { position: absolute; display: flex; align-items: center; }
  .brand-dot { border-radius: 50%; background: var(--accent-yellow); flex: none; }
  .brand-name {
    font-weight: 600;
    text-transform: uppercase;
    line-height: 1.15;
  }
  .brand-name span { display: block; }

  .brand-front { left: 36px; top: 62px; gap: 26px; }
  .brand-front .brand-dot { width: 54px; height: 54px; }
  .brand-front .brand-name { color: var(--text-dark); font-size: 27px; letter-spacing: 2px; }
  .brand-front .brand-name span + span { font-size: 20px; letter-spacing: 5px; }

  .brand-back { left: 72px; top: 152px; gap: 34px; }
  .brand-back .brand-dot { width: 80px; height: 80px; }
  .brand-back .brand-name { color: var(--text-light); font-size: 40px; letter-spacing: 2px; }
  .brand-back .brand-name span + span { font-size: 28px; letter-spacing: 7px; }

  .holder-name {
    position: absolute; left: 28px; top: 268px;
    color: var(--text-light);
    font-size: 21px; font-weight: 600;
    letter-spacing: 2.5px;
    font-variant: small-caps;
  }
  .contact-list {
    position: absolute; right: 18px; top: 240px;
    list-style: none;
    color: var(--text-light);
    font-size: 19px; font-weight: 400;
    text-align: right;
  }
  .contact-item { display: flex; justify-content: flex-end; align-items: flex-start; gap: 12px; line-height: 28px; }
  .contact-item + .contact-item { margin-top: 4px; }
  .contact-item.phone { margin-top: 12px; }
  .contact-icon { width: 18px; height: 18px; margin-top: 5px; flex: none; }

  .back-pattern { position: absolute; left: 0; top: 0; }
</style>
</head>
<body>

<section class="card card-front">
  <div class="front-header">
    <svg width="742" height="214" viewBox="0 0 742 214">
      <path class="accent-swoosh" d="M0 196 L420 196 Q520 150 570 126 Q480 176 420 206 L0 206 Z" fill="var(--accent-yellow)"/>
      <path role="img" aria-label="Dark skyline of industrial buildings rising toward the right edge" d="M432 214 Q560 180 620 40 L742 40 L742 214 Z" fill="var(--charcoal)"/>
    </svg>
    <div class="brand brand-front">
      <div class="brand-dot"></div>
      <div class="brand-name"><span>Ridgepost</span><span>Contractors LLC.</span></div>
    </div>
  </div>

  <div class="holder-name">Derek T.Holloway</div>

  <ul class="contact-list">
    <li class="contact-item address">
      <span>4837 Tamarind<br>Dr. Colorado Springs,<br>CO. 80917</span>
      <svg class="contact-icon" viewBox="0 0 18 18"><circle cx="9" cy="9" r="9" fill="var(--icon-red)"/><path d="M4 9.5 L9 5 L14 9.5 H12.5 V13 H5.5 V9.5 Z" fill="#fff"/></svg>
    </li>
    <li class="contact-item phone">
      <span>406 - 555 - 0148</span>
      <svg class="contact-icon" viewBox="0 0 18 18"><circle cx="9" cy="9" r="9" fill="var(--icon-red)"/><rect x="6" y="4" width="6" height="10" rx="1" fill="#fff"/><rect x="7" y="5.5" width="4" height="5" fill="var(--icon-red)"/></svg>
    </li>
    <li class="contact-item email">
      <span>derek@ridgepostcontractors.com</span>
      <svg class="contact-icon" viewBox="0 0 18 18"><circle cx="9" cy="9" r="9" fill="var(--icon-red)"/><rect x="4" y="5.5" width="10" height="7" fill="#fff"/><path d="M4 5.5 L9 9.5 L14 5.5" stroke="var(--icon-red)" stroke-width="1.2" fill="none"/></svg>
    </li>
  </ul>
</section>

<section class="card card-back">
  <svg class="back-pattern" width="742" height="422" viewBox="0 0 742 422">
    <defs>
      <linearGradient id="backPatternFill" x1="0" y1="0" x2="0" y2="1">
        <stop offset="0" stop-color="var(--pattern-tone)" stop-opacity="0.9"/>
        <stop offset="1" stop-color="var(--pattern-tone)" stop-opacity="0.2"/>
      </linearGradient>
    </defs>
    <path role="img" aria-label="Faint perspective outline of tall buildings behind the brand name" d="M0 360 L260 20 L360 70 L480 120 L742 390 Z" fill="url(#backPatternFill)"/>
  </svg>
  <div class="brand brand-back">
    <div class="brand-dot"></div>
    <div class="brand-name"><span>Ridgepost</span><span>Contractors LLC.</span></div>
  </div>
</section>

</body>
</html>
```